Northfield Builders Guild Business card

We are looking for a new business card design with photo included.
Our business is a nonprofit construction contractor membership organization. We offer business education, assist with business setup and licensing, provide safety training, and provide a member directory.
URL: www.builderslinkguild.org
Color code:
CMYK: 0 cyan, 42 magenta, 100 yellow, 0 black for Print.
Hexidecimal: #FF9900
RGB: R 255; G 153; B 0

```html
<!DOCTYPE html>
<html lang="en">
<head>
<meta charset="utf-8">
<title>Northfield Builders Guild – Business Card</title>
<link href="https://fonts.googleapis.com/css2?family=Montserrat:wght@400;500;600;800&display=swap" rel="stylesheet">
<style>
  :root {
    --orange: #f7941d;
    --charcoal: #353435;
    --charcoal-light: #474647;
    --white: #ffffff;
    --backdrop: #dcdcdc;
    --ink: #2f2e2f;
  }
  * { box-sizing: border-box; margin: 0; padding: 0; }
  html, body {
    width: 1200px; height: 1200px; overflow: hidden;
    background: var(--backdrop);
    font-family: "Montserrat", sans-serif;
  }
  .card {
    position: absolute;
    left: 262px;
    width: 686px; height: 392px;
    border-radius: 22px;
    overflow: hidden;
  }
  .card--front { top: 165px; background: var(--white); }
  .card--back  { top: 653px; background: var(--orange); }

  .card__panel { position: absolute; inset: 0; }

  .brand {
    position: absolute;
    text-align: center;
    font-weight: 800;
    color: var(--ink);
    line-height: 1.02;
    letter-spacing: -0.5px;
  }
  .brand--front { left: 30px; width: 230px; top: 160px; font-size: 30px; }
  .brand--back  { left: 0; width: 686px; top: 130px; font-size: 52px; }

  .contact {
    position: absolute; left: 384px; top: 82px;
    color: var(--white);
  }
  .contact__name {
    color: var(--orange);
    font-size: 24px; font-weight: 500;
    letter-spacing: 0.3px;
  }
  .contact__title { font-size: 16px; font-weight: 600; margin-top: 1px; }
  .contact__address { font-size: 16px; line-height: 20px; margin-top: 14px; }
  .contact__list { list-style: none; margin-top: 14px; font-size: 16px; line-height: 19.5px; }
  .contact__list li { display: flex; align-items: center; gap: 8px; }
  .contact__list svg { width: 14px; height: 14px; flex: none; fill: var(--orange); }

  .back-url {
    position: absolute; left: 0; width: 686px; top: 322px;
    text-align: center;
    color: var(--white);
    font-size: 16px; letter-spacing: 3.4px;
  }
</style>
</head>
<body>

<section class="card card--front">
  <svg class="card__panel" width="686" height="392" viewBox="0 0 686 392" aria-hidden="true">
    <defs>
      <linearGradient id="panelShade" x1="0" y1="0" x2="0" y2="1">
        <stop offset="0" stop-color="var(--charcoal-light)"/>
        <stop offset="1" stop-color="var(--charcoal)"/>
      </linearGradient>
    </defs>
    <path d="M274,0 Q440,196 270,392 L686,392 L686,0 Z" fill="url(#panelShade)"/>
    <path d="M274,0 Q440,196 270,392" fill="none" stroke="var(--orange)" stroke-width="4"/>
  </svg>

  <div class="brand brand--front">NORTHFIELD<br>BUILDERS<br>GUILD</div>

  <div class="contact">
    <p class="contact__name">DANIEL REYES</p>
    <p class="contact__title">President</p>
    <p class="contact__address">2400 Cedar Mill Ave.,<br>Suite #210<br>Springfield, OR 97477</p>
    <ul class="contact__list">
      <li><svg viewBox="0 0 24 24"><path d="M6.6 10.8a15 15 0 0 0 6.6 6.6l2.2-2.2a1 1 0 0 1 1-.25 11.4 11.4 0 0 0 3.6.57 1 1 0 0 1 1 1V20a1 1 0 0 1-1 1A17 17 0 0 1 3 4a1 1 0 0 1 1-1h3.5a1 1 0 0 1 1 1c0 1.25.2 2.45.57 3.57a1 1 0 0 1-.25 1z"/></svg>(541) 555-0184</li>
      <li><svg viewBox="0 0 24 24"><path d="M7 1h10a2 2 0 0 1 2 2v18a2 2 0 0 1-2 2H7a2 2 0 0 1-2-2V3a2 2 0 0 1 2-2zm0 3v15h10V4z"/></svg>541.555.0127</li>
      <li><svg viewBox="0 0 24 24"><path d="M2 5h20v14H2zm2 2v.5l8 5 8-5V7z"/></svg>support@nbguild.org</li>
      <li><svg viewBox="0 0 24 24"><circle cx="12" cy="12" r="10"/><path d="M7 8c2 0 3 1 3 3s2 2 2 4-1 3-1 5M15 4c0 2 1 3 3 3" fill="none" stroke="var(--charcoal)" stroke-width="1.6"/></svg>builderslinkguild.org</li>
    </ul>
  </div>
</section>

<section class="card card--back">
  <div class="brand brand--back">NORTHFIELD<br>BUILDERS GUILD</div>
  <p class="back-url">www.builderslinkguild.org</p>
</section>

</body>
</html>
```